Laser Tattoo Removal Business Cards

We are looking for a professional business card design for a laser tattoo removal business. Ideally looking for a black business card design. The name of the business is Brightline Tattoo Removal. We place our cards at local tattoo shops so we ideally are looking for something trendy/edgy to draw both male and female clientele in.

Target Market(s)

Male/Female ages 18-60

Contact Information for Business Card

black background ideally.. hoping to stay within greys, whites and black

Font styles to use
Serif
Sans Serif

Colors
121212
a9a9a9
5c5c5c
f5f5f5
ffffff
7f7f7f
606060
848484
9d9d9d

Requirements
Must have
• Employee Info:
• Melissa Thornbury
• Chief Executive Offer
• m: 919.537.2846
• w: 919.362.4178
• f: 919.685.3907
• mthornbury@brightlinetattooremoval.example
• Address:
• 4615 Oakmere Pkwy, Suite 210
• Raleigh, NC 27654
• Website:
• www.brightlinetattooremoval.example
Nice to have
• Myabe business name on back or logo on back and employee info on the front

```html
<!DOCTYPE html>
<html lang="en">
<head>
<meta charset="utf-8">
<title>Brightline Tattoo Removal – Business Cards</title>
<link rel="stylesheet" href="https://fonts.googleapis.com/css2?family=Roboto:wght@400;500;700&display=swap">
<style>
  :root {
    --page: #e6e6e6;
    --card-white: #f5f5f5;
    --card-black: #121212;
    --band-light: #8e8e8e;
    --band-dark: #333333;
    --ink: #1e1e1e;
    --ink-soft: #5c5c5c;
    --muted: #9d9d9d;
    --rule: #a9a9a9;
    --white: #ffffff;
  }
  * { box-sizing: border-box; margin: 0; padding: 0; }
  html, body { width: 1200px; height: 960px; overflow: hidden; }
  body {
    background: var(--page);
    font-family: "Roboto", Arial, sans-serif;
    position: relative;
  }
  .card {
    position: absolute;
    left: 300px;
    width: 600px;
    height: 340px;
    overflow: hidden;
    box-shadow: 0 2px 8px rgba(0,0,0,0.25);
  }
  .card--front { top: 112px; background: var(--card-white); }
  .card--back { top: 478px; background: var(--card-black); }
  .card__bands { position: absolute; inset: 0; width: 100%; height: 100%; }

  .brand-name {
    position: absolute;
    font-weight: 500;
    text-transform: uppercase;
    letter-spacing: 3px;
    line-height: 1.35;
    text-align: center;
    font-size: 19px;
  }
  .card--front .brand-name { left: 20px; top: 140px; width: 240px; color: var(--ink); }
  .card--back .brand-name { left: 340px; top: 210px; width: 240px; color: var(--white); }

  .divider {
    position: absolute;
    left: 272px; top: 76px;
    width: 1px; height: 196px;
    background: var(--rule);
  }
  .contact { position: absolute; left: 292px; top: 80px; color: var(--ink-soft); }
  .contact__name {
    font-size: 18px; font-weight: 700; color: var(--ink);
    text-transform: uppercase; letter-spacing: 0.3px;
  }
  .contact__title { font-size: 14px; color: var(--muted); margin-top: 1px; }
  .contact__address { font-size: 13.5px; line-height: 19px; margin-top: 13px; color: #333; }
  .contact__list { list-style: none; margin-top: 10px; font-size: 13.5px; color: #333; }
  .contact__list li { display: flex; align-items: center; height: 19px; }
  .contact__list li.email, .contact__list li.web { font-size: 12.5px; }
  .contact__icon { width: 12px; height: 12px; margin-right: 10px; fill: var(--ink); flex: none; }
</style>
</head>
<body>

<section class="card card--front" aria-label="Business card front">
  <svg class="card__bands" viewBox="0 0 600 340" preserveAspectRatio="none" aria-hidden="true">
    <polygon points="0,0 600,0 0,52" fill="var(--band-light)"/>
    <polygon points="600,290 600,340 0,340" fill="var(--band-dark)"/>
  </svg>

  <div class="brand-name">Brightline<br>Tattoo Removal</div>
  <div class="divider"></div>

  <div class="contact">
    <h1 class="contact__name">Melissa Thornbury</h1>
    <p class="contact__title">Chief Executive Offer</p>
    <p class="contact__address">4615 Oakmere Pkwy, Suite 210<br>Raleigh, NC 27654</p>
    <ul class="contact__list">
      <li class="phone">
        <svg class="contact__icon" viewBox="0 0 12 12"><path d="M2.3 0.5 L4 2.6 L3.1 4 C3.7 5.5 5 6.8 6.5 7.4 L7.9 6.5 L10 8.2 L8.9 10.6 C4.6 10.3 1.4 6.8 0.9 2.4 Z"/></svg>
        919.362.4178
      </li>
      <li class="mobile">
        <svg class="contact__icon" viewBox="0 0 12 12"><path d="M3 0 H9 V12 H3 Z M4 1.5 V9.5 H8 V1.5 Z" fill-rule="evenodd"/></svg>
        919.537.2846
      </li>
      <li class="fax">
        <svg class="contact__icon" viewBox="0 0 12 12"><rect x="3" y="1" width="6" height="3"/><rect x="0.5" y="4.5" width="11" height="5" rx="1"/><rect x="3" y="8" width="6" height="3" fill="#fff"/><rect x="3.6" y="8.6" width="4.8" height="1.8"/></svg>
        919.685.3907
      </li>
      <li class="email">
        <svg class="contact__icon" viewBox="0 0 12 12"><rect x="0.5" y="2.5" width="11" height="7"/><path d="M0.5 2.5 L6 6.5 L11.5 2.5" fill="none" stroke="#fff" stroke-width="1"/></svg>
        mthornbury@brightlinetattooremoval.example
      </li>
      <li class="web">
        <svg class="contact__icon" viewBox="0 0 12 12"><circle cx="6" cy="6" r="5.5"/><path d="M0.5 6 H11.5 M6 0.5 C3.5 3 3.5 9 6 11.5 M6 0.5 C8.5 3 8.5 9 6 11.5" fill="none" stroke="#fff" stroke-width="0.8"/></svg>
        www.brightlinetattooremoval.example
      </li>
    </ul>
  </div>
</section>

<section class="card card--back" aria-label="Business card back">
  <div class="brand-name">Brightline<br>Tattoo Removal</div>
</section>

</body>
</html>
```